Need Web Design for Business Process Outsourcing Company (Quorvane)

Quorvane is a business process outsourcing company. Need a simple site similar to http://www.tallowbrinkhire.com/ but with a more professional and credible look. New to the process; not sure where to start and comparing my options. Please let me know what my options are if I choose to go with you. Logo is attached for your reference. Please use same colorway

Reason: I want the final product to be coded. Please confirm you will be able to code final design.

Industry/Entity Type

Business

Coding

Coded - Design and coding required

```html
<!DOCTYPE html>
<html lang="en">
<head>
<meta charset="utf-8">
<title>Quorvane Services – Business Process Outsourcing</title>
<link rel="stylesheet" href="https://fonts.googleapis.com/css2?family=Jost:wght@400;500;600;700&display=swap">
<style>
:root{
  --brand:#0a8bcf;
  --brand-dark:#0d4a7a;
  --navy:#0f3d63;
  --ink:#2b2b2b;
  --muted:#555;
  --light:#f4f5f7;
  --line:#d9dde2;
  --white:#fff;
  --logo-grey:#8a8a8a;
}
*{box-sizing:border-box;margin:0;padding:0}
html,body{width:1200px;height:3120px;overflow:hidden;background:var(--white)}
body{font-family:"Jost",Arial,sans-serif;color:var(--ink)}
.page{position:relative;width:1200px;height:3120px;overflow:hidden}
.abs{position:absolute}

/* header */
.hero{position:absolute;left:0;top:0;width:1200px;height:645px;
  background:linear-gradient(180deg,#f3f6f9 0%,#dfe7ee 28%,#b9c7d4 45%,#c9d4de 62%,#e6ecf1 80%,#f1f4f7 100%)}
.brand{position:absolute;display:flex;align-items:center;gap:12px}
.brand-mark{width:64px;height:64px;background:var(--brand);border-radius:6px}
.brand-name{font-weight:600;font-size:42px;line-height:1;color:var(--navy)}
.brand-sub{font-size:15px;letter-spacing:14px;color:var(--navy);margin-top:4px}
.callbox{left:728px;top:25px;width:208px;height:37px;border:1px solid var(--line);background:var(--white);
  display:flex;align-items:center;gap:8px;padding-left:14px;font-size:10px;color:var(--muted)}
.callbox b{color:var(--brand);font-size:13px;font-weight:600}
.searchbox{left:953px;top:25px;width:116px;height:37px;border:1px solid var(--line);background:var(--white);
  display:flex;align-items:center;gap:8px;padding-left:12px;font-size:10px;color:var(--muted)}
.nav{left:578px;top:83px;display:flex;align-items:center;font-size:13px;font-weight:500;color:#111}
.nav a{color:inherit;text-decoration:none;margin-right:56px}
.nav a.active{background:var(--brand);color:var(--white);padding:8px 14px;margin-right:40px}
.hero-title{left:129px;top:506px;color:var(--white);font-weight:700;font-size:34px;line-height:42px;
  text-shadow:0 2px 6px rgba(0,0,0,.35)}
.dots{left:547px;top:578px;display:flex;gap:10px}
.dots span{width:11px;height:11px;border-radius:50%;background:rgba(255,255,255,.8)}
.dots span.on{background:transparent;border:2px solid var(--white)}
.hero-wave{left:0;top:595px}

/* section titles */
.section-title{position:absolute;left:0;width:1200px;text-align:center;font-weight:700;font-size:24px;color:var(--navy)}
.section-title::after{content:"";display:block;width:84px;height:3px;background:var(--brand);margin:14px auto 0}

/* services */
.service{position:absolute;width:330px}
.service svg{position:absolute;left:0;top:0}
.service-body{position:absolute;left:81px;top:0;width:240px}
.service h3{font-weight:500;font-size:15px;color:var(--navy);letter-spacing:.2px}
.service p{font-size:12px;line-height:20px;color:var(--muted);margin-top:14px;width:180px}
.btn-small{display:inline-block;background:var(--brand);color:var(--white);font-size:9px;font-weight:600;
  width:75px;height:25px;line-height:25px;text-align:center;margin-top:20px}

/* stats */
.stats{position:absolute;left:0;top:1238px;width:1200px;height:243px;
  background:linear-gradient(90deg,#1f5d92 0%,#3d78a8 35%,#2e6a9c 65%,#1b5a90 100%)}
.stat{position:absolute;top:68px;width:240px;margin-left:-120px;text-align:center;color:var(--white)}
.stat strong{display:block;font-weight:400;font-size:42px;line-height:50px}
.stat span{display:block;font-size:15px;margin-top:14px}

/* news */
.news-photo{left:166px;top:1550px;width:328px;height:441px;border:2px solid #8fc3e6;padding:8px;background:var(--white)}
.news-photo div{width:100%;height:100%;background:linear-gradient(160deg,#e9ecef 0%,#c8cdd3 45%,#9aa3ad 70%,#d8dbdf 100%)}
.news-title{left:562px;top:1552px;font-weight:700;font-size:24px;color:var(--navy)}
.news-title::after{content:"";display:block;width:84px;height:3px;background:var(--brand);margin-top:14px}
.news-date{left:562px;top:1640px;background:#eceeef;font-size:9px;color:#666;padding:5px 14px}
.news-head{left:562px;top:1690px;width:470px;font-size:15px;line-height:24px;color:var(--brand);font-weight:500}
.news-text{left:562px;top:1752px;width:462px;font-size:14px;line-height:24px;color:#333;text-align:justify}
.btn{display:inline-block;background:var(--brand);color:var(--white);font-size:11px;font-weight:600;text-align:center}
.news-btn{left:564px;top:1868px;width:114px;height:42px;line-height:42px}
.news-arrows{left:566px;top:1958px}

/* why */
.why{position:absolute;left:0;top:2132px;width:1200px;height:323px;background:var(--brand);border-top:4px solid var(--brand-dark)}
.why-mark{left:697px;top:2070px;width:322px;height:322px;background:var(--white)}
.why h2{position:absolute;left:129px;top:58px;color:var(--white);font-size:22px;font-weight:700}
.why p{position:absolute;left:129px;top:130px;width:454px;color:var(--white);font-size:13px;line-height:22px;text-align:justify}
.why .btn{position:absolute;left:129px;top:231px;width:123px;height:42px;line-height:42px;background:var(--navy)}

/* clients */
.clients{position:absolute;left:0;top:2455px;width:1200px;height:280px;background:var(--light)}
.clients .section-title{top:60px}
.client{position:absolute;top:170px;width:180px;margin-left:-90px;text-align:center;font-size:34px;font-weight:500;color:var(--logo-grey)}

/* footer */
.footer-brand{left:129px;top:2798px}
.follow{left:185px;top:2932px;width:200px;text-align:center;font-size:13px;font-weight:600;color:#222}
.social{left:230px;top:2970px;display:flex;gap:12px}
.social span{width:30px;height:30px;border-radius:50%}
.foot-head{font-size:12px;font-weight:600;color:#222}
.contact-row{position:absolute;left:555px;display:flex;gap:22px;font-size:12px;line-height:22px;color:#444}
.contact-row i{width:30px;height:30px;border-radius:50%;background:var(--brand);flex:none;display:flex;align-items:center;justify-content:center}
.field{position:absolute;left:832px;width:235px;border:1px solid #cfd4d9;font-size:10px;color:#777;padding:6px 10px;background:var(--white)}
.submit{position:absolute;left:982px;top:2987px;width:85px;height:30px;line-height:30px;background:var(--navy);color:var(--white);text-align:center;font-size:12px;font-weight:600}
.rule{left:129px;top:3058px;width:942px;height:1px;background:#dde0e3}
.copyright{left:0;top:3082px;width:1200px;text-align:center;font-size:10px;color:#555}
</style>
</head>
<body>
<div class="page">

  <!-- Header & hero -->
  <section class="hero" role="img" aria-label="Photo of a businessman on a glass balcony overlooking a city skyline"></section>

  <div class="brand" style="left:129px;top:32px">
    <span class="brand-mark"></span>
    <div><div class="brand-name">Quorvane</div><div class="brand-sub">SERVICES</div></div>
  </div>

  <div class="abs callbox">
    <svg width="18" height="14" viewBox="0 0 18 14"><path d="M2 5c4-4 10-4 14 0l-2 3-3-1V5H7v2L4 8z" fill="#0a8bcf"/></svg>
    CALL US : <b>(555) 014.2290</b>
  </div>
  <div class="abs searchbox">
    <svg width="10" height="10" viewBox="0 0 10 10"><circle cx="4" cy="4" r="3" fill="none" stroke="#333" stroke-width="1.4"/><path d="M6.3 6.3 9 9" stroke="#333" stroke-width="1.4"/></svg>
    SEARCH
  </div>

  <nav class="abs nav">
    <a class="active">HOME</a><a>ABOUT US</a><a>SERVICES</a><a>BLOG</a><a style="margin-right:0">CONTACT US</a>
  </nav>

  <h1 class="abs hero-title">BPO BUSINESS PROCESS<br>OUTSOURCING</h1>
  <div class="abs dots"><span></span><span class="on"></span><span></span><span></span><span></span></div>
  <svg class="abs hero-wave" width="1200" height="60" viewBox="0 0 1200 60">
    <path d="M0 0Q600 40 1200 0V60H0Z" fill="#fff"/>
    <path d="M0 0Q600 40 1200 0" fill="none" stroke="#0a6fb0" stroke-width="9"/>
    <path d="M0 8Q600 48 1200 8" fill="none" stroke="#8fc3e6" stroke-width="2"/>
  </svg>

  <!-- Services -->
  <h2 class="section-title" style="top:700px">OUR SERVICES</h2>

  <div class="service" style="left:129px;top:812px">
    <svg width="56" height="50" viewBox="0 0 56 50"><path d="M4 14h16l4 5h26v26H4z" fill="#0a8bcf"/><circle cx="40" cy="12" r="9" fill="none" stroke="#0a8bcf" stroke-width="4"/></svg>
    <div class="service-body"><h3>SOFTWARE DEVELOPMENT</h3><p>There are many variations of passages of Lorem Ipsum.</p><span class="btn-small">READ MORE</span></div>
  </div>
  <div class="service" style="left:489px;top:812px">
    <svg width="56" height="50" viewBox="0 0 56 50"><rect x="5" y="5" width="42" height="40" fill="none" stroke="#0a8bcf" stroke-width="2"/><path d="M5 19h42M5 32h42M19 5v40M33 5v40" stroke="#0a8bcf" stroke-width="1.5"/><path d="M8 38l12-12 8 6 16-18" fill="none" stroke="#0a8bcf" stroke-width="3"/></svg>
    <div class="service-body"><h3>WEB ANALYTICS</h3><p>Lorem Ipsum is simply dummy text of the printing.</p><span class="btn-small">READ MORE</span></div>
  </div>
  <div class="service" style="left:807px;top:812px">
    <svg width="66" height="50" viewBox="0 0 66 50"><circle cx="14" cy="14" r="10" fill="none" stroke="#0a8bcf" stroke-width="4" stroke-dasharray="5 3"/><rect x="26" y="22" width="34" height="22" fill="none" stroke="#0a8bcf" stroke-width="2.5"/><path d="M20 47h46" stroke="#0a8bcf" stroke-width="3"/></svg>
    <div class="service-body" style="left:92px"><h3>IT SOLUTIONS</h3><p>It is a long established fact that a reader will be distracted.</p><span class="btn-small">READ MORE</span></div>
  </div>

  <div class="service" style="left:129px;top:1040px">
    <svg width="56" height="50" viewBox="0 0 56 50"><rect x="5" y="4" width="32" height="40" fill="none" stroke="#0a8bcf" stroke-width="2"/><circle cx="24" cy="24" r="11" fill="none" stroke="#0a8bcf" stroke-width="3"/><path d="M32 32l12 12" stroke="#0a8bcf" stroke-width="4"/></svg>
    <div class="service-body"><h3>DATA ANALYTICS</h3><p>There are many variations of passages of Lorem Ipsum</p><span class="btn-small">READ MORE</span></div>
  </div>
  <div class="service" style="left:489px;top:1040px">
    <svg width="56" height="50" viewBox="0 0 56 50"><path d="M4 8h8l6 26h26l6-18H14" fill="none" stroke="#0a8bcf" stroke-width="3"/><circle cx="22" cy="42" r="4" fill="#0a8bcf"/><circle cx="40" cy="42" r="4" fill="#0a8bcf"/></svg>
    <div class="service-body"><h3>E-COMMERCE SERVICES</h3><p>The standard chunk of Lorem Ipsum used since the .</p><span class="btn-small">READ MORE</span></div>
  </div>
  <div class="service" style="left:807px;top:1040px">
    <svg width="66" height="50" viewBox="0 0 66 50"><circle cx="33" cy="8" r="6" fill="#0a8bcf"/><path d="M33 16v10M12 26h42M12 26v8M33 26v8M54 26v8" stroke="#0a8bcf" stroke-width="2.5" fill="none"/><circle cx="12" cy="40" r="5" fill="#0a8bcf"/><circle cx="33" cy="40" r="5" fill="#0a8bcf"/><circle cx="54" cy="40" r="5" fill="#0a8bcf"/></svg>
    <div class="service-body" style="left:92px"><h3>LEAD GENERATION</h3><p>Lorem ipsum dolor sit amet, consectetur adipiscing elit.</p><span class="btn-small">READ MORE</span></div>
  </div>

  <!-- Stats -->
  <section class="stats" role="img" aria-label="Blue-tinted photo of a business team in a meeting">
    <div class="stat" style="left:206px"><strong>75%</strong><span>ONLINE MARKETING</span></div>
    <div class="stat" style="left:455px;top:52px"><strong>1258+</strong><span>CLIENTS</span></div>
    <div class="stat" style="left:711px;top:52px"><strong>35+</strong><span>WORLDWIDE</span></div>
    <div class="stat" style="left:996px;top:52px"><strong>11258+</strong><span>OUTSOURCING</span></div>
  </section>

  <!-- Latest news -->
  <div class="abs news-photo"><div role="img" aria-label="Photo of two business people shaking hands"></div></div>
  <h2 class="abs news-title">LATEST NEWS</h2>
  <span class="abs news-date">14 Nov, 2016</span>
  <h3 class="abs news-head">CONTRARY TO POPULAR BELIEF, LOREM IPSUM IS NOT SIMPLY RAN DOM TEXT. IT HAS ROOTS IN A PIECE OF CLASSICAL</h3>
  <p class="abs news-text">There are many variations of passages of Lorem Ipsum available, but the majority have suffered alteration in some form, by injected humour, or randomised words which don't look even slightly believable. If you are going to use a passage.</p>
  <span class="abs btn news-btn">READ MORE</span>
  <svg class="abs news-arrows" width="60" height="30" viewBox="0 0 60 30"><path d="M12 4 3 15l9 11M36 4l9 11-9 11" fill="none" stroke="#9aa3ad" stroke-width="3"/></svg>

  <!-- Why -->
  <section class="why">
    <h2>WHY QUORVANE</h2>
    <p>There are many variations of passages of Lorem Ipsum available, but the majority have suffered alteration in some form, by injected humour, or randomised words which don't.</p>
    <span class="btn">CONTACT US</span>
  </section>
  <div class="abs why-mark" aria-hidden="true"></div>

  <!-- Clients -->
  <section class="clients">
    <h2 class="section-title">OUR CLIENTS</h2>
    <div class="client" style="left:171px">Norvex</div>
    <div class="client" style="left:389px">Altrix</div>
    <div class="client" style="left:610px">Wendal</div>
    <div class="client" style="left:830px">Pellow</div>
    <div class="client" style="left:1019px">Marsq</div>
  </section>

  <!-- Footer -->
  <div class="brand footer-brand">
    <span class="brand-mark"></span>
    <div><div class="brand-name">Quorvane</div><div class="brand-sub">SERVICES</div></div>
  </div>
  <div class="abs follow">FOLLOW US</div>
  <div class="abs social" aria-label="Social links">
    <span style="background:#3b5998"></span><span style="background:#1da1f2"></span><span style="background:#dd4b39"></span>
  </div>

  <div class="abs foot-head" style="left:555px;top:2786px">CONTACT US</div>
  <div class="contact-row" style="top:2830px">
    <i><svg width="12" height="16" viewBox="0 0 12 16"><path d="M6 0a6 6 0 0 1 6 6c0 4-6 10-6 10S0 10 0 6a6 6 0 0 1 6-6z" fill="#fff"/><circle cx="6" cy="6" r="2.2" fill="#0a8bcf"/></svg></i>
    <span>2470 Larkmere Lane<br>Dayton, OH 45402</span>
  </div>
  <div class="contact-row" style="top:2888px">
    <i><svg width="14" height="14" viewBox="0 0 14 14"><path d="M3 0l3 3-2 2c1 2 3 4 5 5l2-2 3 3-2 3C6 14 0 8 0 3z" fill="#fff"/></svg></i>
    <span style="line-height:30px">t : (555) 014.2290</span>
  </div>
  <div class="contact-row" style="top:2934px">
    <i><svg width="14" height="10" viewBox="0 0 14 10"><rect width="14" height="10" fill="#fff"/><path d="M0 0l7 6 7-6" fill="none" stroke="#0a8bcf" stroke-width="1.4"/></svg></i>
    <span style="line-height:30px">e : info@Quorvane.com</span>
  </div>

  <div class="abs foot-head" style="left:832px;top:2786px">GET A QUOTE</div>
  <div class="field" style="top:2818px;height:32px">Name</div>
  <div class="field" style="top:2862px;height:34px">E mail</div>
  <div class="field" style="top:2906px;height:69px">Message</div>
  <div class="submit">SUBMIT</div>

  <div class="abs rule"></div>
  <div class="abs copyright">Copyrights @ 2016 All Rights Reserved</div>
</div>
</body>
</html>
```